Front page of Orthodox Christian Monastery Website

I am attaching a couple of versions of design that was already created for the front page of the website. You can grab the same pictures and titles (do not need to know the Russian language) to create your own version of design.
Background: Monastery website contains sermons, stories about monastery life, monastery music of the sisterhood.
Main principles of the design:
1. Various materials/sermons/music have to be clearly visible immediately to the site visitor.
2. Text descriptions to photos should be using font with a good contrast, highly clickable and easily readable.
3. Every article should have a photo or a quality picture (use those in the sample) that will convey something about it.
4. On the top, there will be a menu, which will be a line of words (just use generic words for now).
5. Design should reflect Christian Orthodox themes and fonts.
Updates

Target Market(s)

Orthodox Christian believers around the world and those that are interested in Orthodox Christianity

Number of Pages Required

1 page

Font styles to use
Serif

Colors

Designer to choose colors to be used in the design.

Requirements
Must have
• In the project description
Nice to have
• for some ideas see a popular Orthodox Christian website:
• www.verenskaya-lampada.ru
• We don't want to copy it, but it could give ideas.
Should not have
• Should not be overly complex

```html
<!DOCTYPE html>
<html lang="en">
<head>
<meta charset="utf-8">
<title>Orthodox Christian Monastery</title>
<link href="https://fonts.googleapis.com/css2?family=Playfair+Display:wght@400;700&family=Open+Sans:wght@400;600&display=swap" rel="stylesheet">
<style>
:root{
  --green:#0b3d22;
  --green-deep:#08301a;
  --orange:#ee9a2a;
  --card:#e5e5e5;
  --ink:#1e1e1e;
  --muted:#6b6b6b;
  --white:#ffffff;
  --line:#3c6a50;
}
*{box-sizing:border-box;margin:0;padding:0}
html,body{width:1200px;height:2885px;overflow:hidden}
body{background:var(--white);font-family:"Open Sans",Arial,sans-serif;color:var(--ink);position:relative}
a{color:inherit;text-decoration:none}

.site-title{position:absolute;top:22px;left:0;width:1200px;text-align:center;font-family:"Playfair Display",Georgia,serif;font-size:40px;font-weight:400;color:var(--green);letter-spacing:.5px}

.hero{position:absolute;top:108px;left:0;width:1200px;height:507px;background:linear-gradient(180deg,#5f86b8 0%,#9cb6d3 30%,#6b6f58 55%,#2b2a22 80%,#3c3a30 100%)}
.hero-caption{position:absolute;left:0;bottom:0;width:100%;height:100px;background:rgba(235,235,235,.82);padding:18px 133px 0}
.hero-caption h2{font-family:"Playfair Display",Georgia,serif;font-size:21px;font-weight:400;color:var(--ink);margin-bottom:8px}
.hero-caption p{font-size:11.5px;line-height:17px;color:#333;width:934px}
.hero-arrow{position:absolute;top:550px;width:22px;height:30px}
.hero-arrow.prev{left:40px}.hero-arrow.next{right:40px}

.main-nav{position:absolute;top:87px;left:133px;width:934px;height:36px;background:var(--orange);display:flex;align-items:center;padding:0 8px;font-family:"Playfair Display",Georgia,serif;font-size:11.5px;color:#3a2506;letter-spacing:.3px;z-index:2}
.main-nav a{padding:0 14px;height:36px;line-height:36px;white-space:nowrap}
.main-nav a.active{background:#f3b35a;color:var(--white)}
.main-nav .search-icon{margin-left:auto}

.content{position:absolute;top:660px;left:133px;width:667px}
.tabs{position:relative;height:62px;border-bottom:6px solid var(--green);display:flex;align-items:flex-end;gap:6px}
.tabs .wedge{position:absolute;top:0;left:0}
.tab{background:var(--green);color:var(--white);font-family:"Playfair Display",Georgia,serif;font-size:14px;padding:0 14px;height:34px;line-height:34px;white-space:nowrap}
.tab.active{background:var(--card);color:var(--green);border:2px solid var(--green);border-bottom:none}

.article{display:flex;gap:14px;background:var(--card);height:162px;padding:8px;margin-top:13px}
.article .thumb{width:206px;height:146px;flex:none}
.article .date{font-family:"Playfair Display",Georgia,serif;font-size:13px;margin:4px 0 10px}
.article h3{font-size:13.5px;font-weight:400;line-height:18px;margin-bottom:10px;color:#111}
.article p{font-size:9.5px;line-height:15px;color:var(--muted)}

.btn{display:inline-block;font-family:"Playfair Display",Georgia,serif;font-size:12px;border:1.5px solid var(--green);color:var(--green);padding:6px 14px;background:var(--white);white-space:nowrap}
.btn.light{border-color:#b9c9bf;color:var(--white);background:transparent}
.view-more{margin-top:16px}

.panel{position:relative;background:var(--green);color:var(--white)}
.panel .wedge{position:absolute;top:-14px;left:0;width:100%;height:28px}
.panel-title{font-family:"Playfair Display",Georgia,serif;font-size:20px;font-weight:400;text-align:center;position:relative}

.videos{margin-top:32px;height:361px;padding:28px 15px 0}
.video-row{display:flex;gap:9px;margin-top:22px}
.video{width:152px}
.video .thumb{height:119px;position:relative}
.video .thumb svg{position:absolute;left:62px;top:46px}
.video .info{background:var(--white);color:var(--ink);height:96px;padding:14px 14px}
.video .date{font-family:"Playfair Display",Georgia,serif;font-size:12px;margin-bottom:8px}
.video p{font-size:9.5px;line-height:14px;color:var(--muted)}
.videos .btn{display:block;width:max-content;margin:20px auto 0;text-align:center}

.audios{margin-top:34px;height:120px;padding:12px 15px 0}
.audios .panel-title{font-size:19px}
.audios .sub{font-size:9.5px;text-align:center;color:#cfdcd4;margin-top:2px}
.player{display:flex;align-items:center;gap:14px;margin-top:14px}
.track{flex:1;height:5px;background:#3b5a48;position:relative}
.track span{position:absolute;left:0;top:0;height:5px;width:43%;background:var(--orange)}

.sidebar{position:absolute;top:660px;left:823px;width:244px;display:flex;flex-direction:column;gap:28px}
.side-panel{padding:22px 10px 16px}
.side-panel .panel-title{margin-bottom:12px}
.side-item{display:flex;gap:10px;background:var(--card);color:var(--ink);padding:5px;height:94px;margin-bottom:8px}
.side-item .thumb{width:77px;height:84px;flex:none;position:relative}
.side-item .date{font-family:"Playfair Display",Georgia,serif;font-size:12px;margin:8px 0 8px}
.side-item p{font-size:9px;line-height:13px;color:var(--muted)}
.side-panel .btn{display:block;width:max-content;margin:12px auto 0;text-align:center}
.about-wrap{background:var(--card);padding:6px}
.about-photo{height:150px;background:linear-gradient(180deg,#c9cdd2,#2c2c2f)}
.about-text{color:var(--muted);font-size:9px;line-height:14px;padding:8px 2px 2px}

.gallery-head{position:absolute;top:2244px;left:0;width:1200px;display:flex;justify-content:center;align-items:center;gap:18px}
.gallery-head h2{font-family:"Playfair Display",Georgia,serif;font-size:25px;font-weight:400;color:var(--green)}
.gbtn{width:22px;height:22px;border:1.5px solid #888;display:flex;align-items:center;justify-content:center}
.gallery{position:absolute;top:2288px;left:0;width:1200px;height:164px;display:flex;gap:3px}
.gallery div{flex:1}

.footer{position:absolute;top:2460px;left:0;width:1200px;height:425px;background:linear-gradient(180deg,#124a2c,var(--green-deep));color:var(--white)}
.footer .wedge{position:absolute;top:-12px;left:0}
.newsletter h2{font-family:"Playfair Display",Georgia,serif;font-size:22px;font-weight:400;text-align:center;padding-top:50px;letter-spacing:.5px}
.subscribe{position:relative;width:934px;margin:16px auto 0;height:36px}
.subscribe:before{content:"";position:absolute;left:0;right:0;top:18px;border-top:1px solid var(--line)}
.subscribe .field{position:absolute;left:288px;width:363px;height:36px;background:var(--white);color:#444;font-size:11.5px;padding:0 14px;line-height:36px}
.subscribe .field svg{position:absolute;right:12px;top:11px}
.foot-cols{display:flex;width:934px;margin:50px auto 0}
.foot-col h4{font-family:"Playfair Display",Georgia,serif;font-size:16px;font-weight:400;margin-bottom:14px}
.foot-col ul{list-style:none;font-size:10.5px;line-height:24px;color:#d6e2da}
.foot-col ul li:before{content:"• ";color:var(--orange)}
.split{display:flex;gap:36px}
.socials{display:flex;gap:6px;margin-top:10px}
.socials span{width:24px;height:24px;border-radius:50%;display:block}
.copyright{position:absolute;bottom:30px;left:0;width:1200px;text-align:center;font-size:11px;color:#c8d6cd}
.copyright:before{content:"";position:absolute;left:133px;right:133px;top:-24px;border-top:1px solid var(--line)}
</style>
</head>
<body>

<h1 class="site-title">Orthodox Christian Monastery</h1>

<section class="hero" role="img" aria-label="Photograph of a white monastery church with dark and golden domes and a gilded angel statue under a blue sky">
  <div class="hero-caption">
    <h2>Nullam lorem urna, tempus eget mollis et, dapibus</h2>
    <p>Suspendisse gravida ornare erat sed pulvinar. Vestibulum luctus ex in egestas fringilla. Fusce nec leo ac urna pulvinar auctor. Mauris bibendum fringilla velit. Nulla in lorem massa pellentesque posuere. Nulla tristique posuere molestie. Aliquam erat volutpat.</p>
  </div>
</section>
<svg class="hero-arrow prev" viewBox="0 0 22 30"><path d="M16 4 6 15l10 11" fill="none" stroke="#555" stroke-width="4"/></svg>
<svg class="hero-arrow next" viewBox="0 0 22 30"><path d="M6 4l10 11L6 26" fill="none" stroke="#555" stroke-width="4"/></svg>

<nav class="main-nav">
  <a class="active">HOME</a><a>ABOUT US</a><a>EVETNS</a><a>MEDIA</a><a>COMMUNITY</a><a>FORUM</a><a>SUPPORT</a><a>SEMINARS</a><a>NEWSLETTER</a><a>SEARCH</a>
  <svg class="search-icon" width="14" height="14" viewBox="0 0 14 14"><circle cx="5.5" cy="5.5" r="4" fill="none" stroke="#3a2506" stroke-width="2"/><path d="M8.5 8.5 13 13" stroke="#3a2506" stroke-width="2"/></svg>
</nav>

<main class="content">
  <div class="tabs">
    <svg class="wedge" width="667" height="20" viewBox="0 0 667 20" preserveAspectRatio="none"><polygon points="0,20 667,0 667,12 0,28" fill="var(--orange)"/></svg>
    <a class="tab active">About Monastery Life</a>
    <a class="tab">Monastery Music of the Sisterhood</a>
    <a class="tab">Sermons</a>
  </div>

  <article class="article">
    <div class="thumb" role="img" aria-label="Photo of elderly hands held together in prayer" style="background:linear-gradient(135deg,#6a4030,#3a2218)"></div>
    <div><div class="date">4 May, 2018</div>
    <h3>Pellentesque blandit lacus eget nunc faucibus, tincidunt eros viverra. Phasellus consequat sagittis nisi suscipit feugiat.</h3>
    <p>Cras eget leo sed nunc hendrerit ultricies eu at nisl. Praesent iaculis faucibus urna sit amet lacinia. Maecenas consequat justo enim, ac mattis massa imperdiet quis. Fusce eget neque elit. Sed augue orci, elementum in magna congue, tincidunt vulputate erat. Aliquam consectetur orci molestie dictum molestie. Proin eget congue nulla, vel tempor diam.</p></div>
  </article>
  <article class="article">
    <div class="thumb" role="img" aria-label="Photo of a bishop in a white headdress seated at a table" style="background:linear-gradient(135deg,#d9d4cc,#5a2a22)"></div>
    <div><div class="date">4 May, 2018</div>
    <h3>Vestibulum condimentum, risus ut posuere cursus, velit justo accumsan sem, lobortis aliquet metus dui eu libero.</h3>
    <p>Cras eget leo sed nunc hendrerit ultricies eu at nisl. Praesent iaculis faucibus urna sit amet lacinia. Maecenas consequat justo enim, ac mattis massa imperdiet quis. Fusce eget neque elit. Sed augue orci, elementum in magna congue, tincidunt vulputate erat. Aliquam consectetur orci molestie dictum molestie. Proin eget congue nulla, vel tempor diam.</p></div>
  </article>
  <article class="article">
    <div class="thumb" role="img" aria-label="Photo of an arched church fresco" style="background:linear-gradient(135deg,#c9a86a,#6e7a4a)"></div>
    <div><div class="date">4 May, 2018</div>
    <h3>Fusce sollicitudin lorem et luctus volutpat. Proin placerat dapibus gravida. In tristique tristique nulla eget hendrerit.</h3>
    <p>Cras eget leo sed nunc hendrerit ultricies eu at nisl. Praesent iaculis faucibus urna sit amet lacinia. Maecenas consequat justo enim, ac mattis massa imperdiet quis. Fusce eget neque elit. Sed augue orci, elementum in magna congue, tincidunt vulputate erat. Aliquam consectetur orci molestie dictum molestie. Proin eget congue nulla, vel tempor diam.</p></div>
  </article>
  <article class="article">
    <div class="thumb" role="img" aria-label="Photo of people working together outdoors in the monastery garden" style="background:linear-gradient(135deg,#8a7a5a,#4a3a28)"></div>
    <div><div class="date">4 May, 2018</div>
    <h3>Maecenas vel tortor accumsan quam varius imperdiet vel eget elit. Aenean facilisis tincidunt lectus, id dictum nisi luctus eget.</h3>
    <p>Cras eget leo sed nunc hendrerit ultricies eu at nisl. Praesent iaculis faucibus urna sit amet lacinia. Maecenas consequat justo enim, ac mattis massa imperdiet quis. Fusce eget neque elit. Sed augue orci, elementum in magna congue, tincidunt vulputate erat. Aliquam consectetur orci molestie dictum molestie. Proin eget congue nulla, vel tempor diam.</p></div>
  </article>
  <article class="article">
    <div class="thumb" role="img" aria-label="Photo of clergy reading beside an icon in a church" style="background:linear-gradient(135deg,#d8c7a0,#3a2c22)"></div>
    <div><div class="date">4 May, 2018</div>
    <h3>Sed tellus ex, imperdiet eget gravida sit amet, volutpat eget turpis. In nec ultricies est. Etiam mattis augue vehicula odio posuere</h3>
    <p>Cras eget leo sed nunc hendrerit ultricies eu at nisl. Praesent iaculis faucibus urna sit amet lacinia. Maecenas consequat justo enim, ac mattis massa imperdiet quis. Fusce eget neque elit. Sed augue orci, elementum in magna congue, tincidunt vulputate erat. Aliquam consectetur orci molestie dictum molestie. Proin eget congue nulla, vel tempor diam.</p></div>
  </article>

  <a class="btn view-more">View More</a>

  <section class="panel videos">
    <svg class="wedge" viewBox="0 0 667 28" preserveAspectRatio="none"><polygon points="330,14 667,0 667,14" fill="var(--orange)"/><polygon points="0,14 667,14 667,28 0,28" fill="var(--green)"/></svg>
    <h2 class="panel-title">Videos</h2>
    <div class="video-row">
      <div class="video"><div class="thumb" role="img" aria-label="Video still of a cathedral at dusk" style="background:linear-gradient(180deg,#4a6fa5,#7a5a3a)"><svg width="28" height="28" viewBox="0 0 28 28"><circle cx="14" cy="14" r="13" fill="#fff"/><polygon points="11,8 20,14 11,20" fill="#111"/></svg></div><div class="info"><div class="date">4 May, 2018</div><p>Etiam elementum, bibendum feugiat massa. Curabitur venenatis.</p></div></div>
      <div class="video"><div class="thumb" role="img" aria-label="Video still of a painted church interior" style="background:linear-gradient(180deg,#b08a5a,#6a3a2a)"><svg width="28" height="28" viewBox="0 0 28 28"><circle cx="14" cy="14" r="13" fill="#fff"/><polygon points="11,8 20,14 11,20" fill="#111"/></svg></div><div class="info"><div class="date">4 May, 2018</div><p>Etiam elementum, bibendum feugiat massa. Curabitur venenatis.</p></div></div>
      <div class="video"><div class="thumb" role="img" aria-label="Video still of an icon in a street shrine" style="background:linear-gradient(180deg,#9a9a90,#4a4a44)"><svg width="28" height="28" viewBox="0 0 28 28"><circle cx="14" cy="14" r="13" fill="#fff"/><polygon points="11,8 20,14 11,20" fill="#111"/></svg></div><div class="info"><div class="date">4 May, 2018</div><p>Etiam elementum, bibendum feugiat massa. Curabitur venenatis.</p></div></div>
      <div class="video"><div class="thumb" role="img" aria-label="Video still of a gathering at a long table" style="background:linear-gradient(180deg,#8a6a4a,#3a2a1e)"><svg width="28" height="28" viewBox="0 0 28 28"><circle cx="14" cy="14" r="13" fill="#fff"/><polygon points="11,8 20,14 11,20" fill="#111"/></svg></div><div class="info"><div class="date">4 May, 2018</div><p>Etiam elementum, bibendum feugiat massa. Curabitur venenatis.</p></div></div>
    </div>
    <a class="btn light">View All</a>
  </section>

  <section class="panel audios">
    <h2 class="panel-title">Audios</h2>
    <p class="sub">Proin a dolor mauris. Vestibulum ante ipsum primis in faucibus orci luctus et ultrices posuere cubilia Curae; Vestibulum eget nisl metus.</p>
    <div class="player">
      <svg width="34" height="34" viewBox="0 0 34 34"><circle cx="17" cy="17" r="16" fill="#fff"/><polygon points="13,9 25,17 13,25" fill="#111"/></svg>
      <div class="track"><span></span></div>
      <svg width="24" height="14" viewBox="0 0 24 14"><polygon points="0,0 10,7 0,14" fill="#fff"/><polygon points="10,0 20,7 10,14" fill="#fff"/><rect x="21" y="0" width="3" height="14" fill="#fff"/></svg>
      <svg width="18" height="16" viewBox="0 0 18 16"><polygon points="0,5 4,5 9,1 9,15 4,11 0,11" fill="#fff"/><path d="M12 4q3 4 0 8M14 2q5 6 0 12" stroke="#fff" fill="none" stroke-width="1.5"/></svg>
    </div>
  </section>
</main>

<aside class="sidebar">
  <section class="panel side-panel">
    <svg class="wedge" viewBox="0 0 244 28" preserveAspectRatio="none"><polygon points="120,14 244,0 244,14" fill="var(--orange)"/><polygon points="0,14 244,14 244,28 0,28" fill="var(--green)"/></svg>
    <h2 class="panel-title">Events</h2>
    <div class="side-item"><div class="thumb" role="img" aria-label="Photo of a lit church at night" style="background:linear-gradient(180deg,#2a3f8a,#c9b48a)"></div><div><div class="date">4 May, 2018</div><p>Duis ornare erat eget magna dapibus, in accumsan quam pharetra.</p></div></div>
    <div class="side-item"><div class="thumb" role="img" aria-label="Photo of a priest in red vestments" style="background:linear-gradient(180deg,#c8502a,#6a1a12)"></div><div><div class="date">4 May, 2018</div><p>Duis ornare erat eget magna dapibus, in accumsan quam pharetra.</p></div></div>
    <div class="side-item"><div class="thumb" role="img" aria-label="Photo of a procession with banners" style="background:linear-gradient(180deg,#8a6a7a,#4a2a2a)"></div><div><div class="date">4 May, 2018</div><p>Duis ornare erat eget magna dapibus, in accumsan quam pharetra.</p></div></div>
    <div class="side-item"><div class="thumb" role="img" aria-label="Photo of a monastery by a lake at sunset" style="background:linear-gradient(180deg,#c87a5a,#2a3a4a)"></div><div><div class="date">4 May, 2018</div><p>Duis ornare erat eget magna dapibus, in accumsan quam pharetra.</p></div></div>
    <a class="btn">View More</a>
  </section>

  <section class="panel side-panel">
    <svg class="wedge" viewBox="0 0 244 28" preserveAspectRatio="none"><polygon points="120,14 244,0 244,14" fill="var(--orange)"/><polygon points="0,14 244,14 244,28 0,28" fill="var(--green)"/></svg>
    <h2 class="panel-title">Seminars</h2>
    <div class="side-item"><div class="thumb" role="img" aria-label="Portrait photo of an elder monk" style="background:linear-gradient(180deg,#9a9a9a,#2a2a2a)"></div><div><div class="date">4 May, 2018</div><p>Duis ornare erat eget magna dapibus, in accumsan quam pharetra.</p></div></div>
    <div class="side-item"><div class="thumb" role="img" aria-label="Photo of a church service" style="background:linear-gradient(180deg,#6a4a6a,#2a1a2a)"></div><div><div class="date">4 May, 2018</div><p>Duis ornare erat eget magna dapibus, in accumsan quam pharetra.</p></div></div>
    <div class="side-item"><div class="thumb" role="img" aria-label="Photo of a white church with domes" style="background:linear-gradient(180deg,#7a9ac8,#8a8a7a)"></div><div><div class="date">4 May, 2018</div><p>Duis ornare erat eget magna dapibus, in accumsan quam pharetra.</p></div></div>
    <div class="side-item"><div class="thumb" role="img" aria-label="Image of a painted icon" style="background:linear-gradient(180deg,#c8a84a,#5a6a2a)"></div><div><div class="date">4 May, 2018</div><p>Duis ornare erat eget magna dapibus, in accumsan quam pharetra.</p></div></div>
    <a class="btn">View More</a>
  </section>

  <section class="panel side-panel">
    <svg class="wedge" viewBox="0 0 244 28" preserveAspectRatio="none"><polygon points="120,14 244,0 244,14" fill="var(--orange)"/><polygon points="0,14 244,14 244,28 0,28" fill="var(--green)"/></svg>
    <h2 class="panel-title">About Us</h2>
    <div class="about-wrap">
      <div class="about-photo" role="img" aria-label="Photo of two nuns in black habits"></div>
      <p class="about-text">Aliquam erat volutpat. Quisque aliquet ex nec est vestibulum pulvinar. Pellentesque convallis molestie enim sit amet efficitur. Etiam id imperdiet lectus. Vivamus lacus justo, ultrices nec erat in, euismod iaculis mauris. Vivamus eleifend vitae nulla vel malesuada. In ac malesuada lacus, et consectetur ante. Fusce vitae lectus sit amet mi pulvinar maximus. Aenean placerat, nibh vel accumsan aliquet, magna nibh accumsan nibh</p>
    </div>
    <a class="btn">Read More</a>
  </section>
</aside>

<div class="gallery-head">
  <span class="gbtn"><svg width="8" height="12" viewBox="0 0 8 12"><path d="M6 1 1 6l5 5" fill="none" stroke="#555" stroke-width="1.5"/></svg></span>
  <h2>Gallery</h2>
  <span class="gbtn"><svg width="8" height="12" viewBox="0 0 8 12"><path d="M2 1l5 5-5 5" fill="none" stroke="#555" stroke-width="1.5"/></svg></span>
</div>
<section class="gallery">
  <div role="img" aria-label="Photo of a priest with a cross at a service" style="background:linear-gradient(135deg,#8a6a3a,#1a1a22)"></div>
  <div role="img" aria-label="Photo of clergy in red vestments before an altar" style="background:linear-gradient(135deg,#c87a6a,#5a2a1a)"></div>
  <div role="img" aria-label="Photo of a liturgy inside a golden church" style="background:linear-gradient(135deg,#b8904a,#3a2a1a)"></div>
  <div role="img" aria-label="Photo of a crowd with flowers outside a church" style="background:linear-gradient(135deg,#8a7a9a,#6a2a3a)"></div>
  <div role="img" aria-label="Black and white photo of a person reading a book" style="background:linear-gradient(135deg,#d8d8d8,#3a3a3a)"></div>
</section>

<footer class="footer">
  <svg class="wedge" width="1200" height="24" viewBox="0 0 1200 24" preserveAspectRatio="none"><polygon points="0,12 600,0 1200,4 1200,14 0,20" fill="var(--orange)"/></svg>
  <div class="newsletter">
    <h2>NEWSLETTER SUBSCRIBE</h2>
    <div class="subscribe"><div class="field">Email Address<svg width="18" height="14" viewBox="0 0 18 14"><rect width="18" height="14" rx="1" fill="var(--green)"/><path d="M1 1l8 6 8-6" fill="none" stroke="#fff" stroke-width="1.5"/></svg></div></div>
  </div>
  <div class="foot-cols">
    <div class="foot-col" style="width:248px"><h4>Menu</h4><div class="split">
      <ul><li>Home</li><li>About Us</li><li>Evetns</li><li>Media</li><li>Community</li></ul>
      <ul><li>Forum</li><li>Support</li><li>Seminars</li><li>Newsletter</li><li>Search</li></ul></div></div>
    <div class="foot-col" style="width:340px"><h4>Information</h4><div class="split">
      <ul><li>Maecenas vel</li><li>Fusce sollicitudin</li><li>Proin placerat</li><li>Pellentesque</li><li>Contact Us</li></ul>
      <ul><li>Terms and conditions of use</li><li>About us</li><li>Sitemap</li></ul></div></div>
    <div class="foot-col" style="width:144px"><h4>More Links</h4>
      <ul><li>Proin a dolor</li><li>Vestibulum</li><li>Curabitur</li><li>Fusce nec</li></ul></div>
    <div class="foot-col"><h4>Contact Us</h4>
      <ul><li>info@monasterylife.org</li></ul>
      <div class="socials"><span style="background:#3b5998"></span><span style="background:#1da1f2"></span><span style="background:#dd4b39"></span><span style="background:#cb2027"></span><span style="background:#f57d00"></span><span style="background:#e52d27"></span></div></div>
  </div>
  <p class="copyright">Copyright © 2018 Orthodox Christian Monastery. All rights reserved.</p>
</footer>

</body>
</html>
```